Telvo Website - endlich neu?!
Aufgabenstellung
Es geht um die Gestaltung der Startseite auf Basis unseres verwendeten Magento-Templates.
Außerdem um die Gestaltung von Visitenkarte und Briefkopf.

```html
<!DOCTYPE html>
<html lang="de">
<head>
<meta charset="utf-8">
<title>Telvo – Visitenkarte</title>
<link rel="stylesheet" href="https://fonts.googleapis.com/css2?family=Noto+Serif:wght@400&display=swap">
<style>
  :root {
    --page: #ffffff;
    --ink: #111111;
    --card-edge: #1a1a1a;
    --card-shadow: #8a8a8a;
    --olive: #666b47;
    --orange: #ffa500;
    --orange-deep: #ff8800;
    --cream: #f8efd8;
    --metal: #dedede;
    --rule: #555555;
  }
  * { margin: 0; padding: 0; box-sizing: border-box; }
  html, body { width: 998px; height: 1200px; overflow: hidden; background: var(--page); }
  body { position: relative; font-family: "Noto Serif", Georgia, serif; color: var(--ink); }

  .card {
    position: absolute;
    left: 101px;
    width: 792px;
    height: 514px;
    background: var(--page);
    border: 1.5px solid var(--card-edge);
    box-shadow: 4px 4px 0 var(--card-shadow);
    overflow: hidden;
  }
  .card--front { top: 66px; }
  .card--back { top: 635px; }
  .card svg { position: absolute; left: 0; top: 0; }

  .brand-name {
    position: absolute;
    left: 58px;
    top: 40px;
    font-size: 100px;
    line-height: 1;
    color: var(--ink);
  }

  .band-art {
    position: absolute;
    left: 0;
    top: 207px;
    width: 695px;
    height: 60px;
    background: linear-gradient(90deg,
      var(--olive) 0%, var(--olive) 14%,
      var(--orange) 20%, var(--orange-deep) 38%,
      var(--cream) 56%, var(--orange) 72%,
      var(--metal) 82%, var(--metal) 100%);
  }

  .contact { position: absolute; left: 184px; top: 278px; font-size: 24px; line-height: 33px; }
  .contact__name { margin-bottom: 31px; }

  .notes-label { position: absolute; left: 146px; top: 56px; font-size: 24px; }

  .pull-art {
    position: absolute;
    left: 542px;
    top: 460px;
    width: 153px;
    height: 48px;
    background: var(--metal);
  }
</style>
</head>
<body>

<section class="card card--front">
  <span class="brand-name">Telvo</span>
  <div class="band-art" role="img" aria-label="Farbiges Reißverschlussband mit Zieher"></div>

  <div class="contact">
    <p class="contact__name">Helga Brandis</p>
    <p>Lindenweg 14, 30159 Hannover</p>
    <p>Tel.: 0511- 55 210 436, Fax: 0511- 55 210 437</p>
    <p>Mail: Helga@telvo.de</p>
    <p>Web: www.telvo.de</p>
  </div>
</section>

<section class="card card--back">
  <svg width="792" height="514" viewBox="0 0 792 514">
    <g class="note-lines" fill="none" stroke="var(--rule)" stroke-width="1.3" stroke-dasharray="5 4">
      <path d="M0 113 Q200 108 400 110 T792 106"/>
      <path d="M0 168 Q60 174 200 170 T500 164 T792 162"/>
      <path d="M0 210 Q250 206 450 207 T792 204"/>
      <path d="M0 262 Q80 270 260 262 T560 258 T792 256"/>
      <path d="M0 306 Q250 302 500 303 T792 300"/>
      <path d="M0 360 Q120 366 300 360 T620 356 T792 355"/>
      <path d="M0 402 Q300 396 520 398 T792 396"/>
      <path d="M0 456 Q150 462 350 456 T650 452 T792 452"/>
      <path d="M0 492 Q250 488 542 484"/>
    </g>
  </svg>

  <p class="notes-label">Notizen:</p>
  <div class="pull-art" role="img" aria-label="Reißverschlusszieher"></div>
</section>

</body>
</html>
```